Shop Front Design

We are Corwick Fusion Stores, a welding products suppliers just north of London.
We would like a banner 4.0m x 1.5m that will be placed above our building entrance to introduce our business to regular and new customers. Info we would like lister:
-Our Logo (CFS logo1)
-Core info: email address, phone number, opening hours
cfsarc@mailvane.net
07412 580 317
Monday to Friday 12:00 - 18:00
Saturday 09:00 - 12:00
-Our core services:
Welders & Consumables
Hire
Industrial Gases
Training Courses
-Our core suppliers logos. I would like to see what impact they would have on the banner
Preferred colour theme orange and grey.

```html
<!DOCTYPE html>
<html lang="en">
<head>
<meta charset="utf-8">
<title>Corwick Fusion Stores – Shop Front Banner</title>
<link rel="stylesheet" href="https://fonts.googleapis.com/css2?family=Montserrat:wght@600;700;800&family=Roboto:wght@400;500;700&family=Roboto+Condensed:wght@700&display=swap">
<style>
  :root {
    --orange: #e2461d;
    --grey-dark: #4a4a4a;
    --white: #ffffff;
    --ink: #3a3a3a;
  }
  html, body { margin: 0; padding: 0; overflow: hidden; background: var(--white); }
  .banner {
    position: relative; width: 1200px; height: 450px; overflow: hidden;
    background: var(--white); font-family: "Roboto", sans-serif;
  }
  .banner-shapes { position: absolute; inset: 0; }
  .brand {
    position: absolute; left: 68px; top: 18px; display: flex; align-items: center; gap: 6px;
    color: var(--orange); font-family: "Montserrat", sans-serif; font-weight: 800;
  }
  .brand-mark { width: 30px; height: 30px; border-radius: 50%; background: var(--orange); }
  .brand-name { line-height: 1; }
  .brand-name .line1 { display: block; font-size: 16px; letter-spacing: 0.5px; }
  .brand-name .line2 { display: block; font-size: 7px; letter-spacing: 1.3px; margin-top: 2px; }
  .contact { position: absolute; top: 18px; display: flex; align-items: center; gap: 14px;
    font-size: 12px; color: var(--ink); letter-spacing: 0.2px; }
  .contact-phone { left: 293px; }
  .contact-email { left: 451px; }
  .contact-icon { width: 32px; height: 32px; border-radius: 50%; background: var(--orange);
    display: flex; align-items: center; justify-content: center; }
  .services-title {
    position: absolute; left: 68px; top: 110px; margin: 0;
    font-family: "Montserrat", sans-serif; font-weight: 700; font-size: 24px;
    color: var(--white); letter-spacing: 0.3px;
  }
  .service { position: absolute; display: flex; align-items: center; gap: 20px; }
  .service-hex { width: 58px; height: 66px; position: relative; }
  .service-hex svg { position: absolute; inset: 0; }
  .service-label { font-family: "Roboto Condensed", sans-serif; font-weight: 700;
    font-size: 16px; color: var(--white); letter-spacing: 0.3px; }
  .svc-gases { left: 67px; top: 171px; }
  .svc-hire { left: 324px; top: 171px; }
  .svc-training { left: 67px; top: 254px; }
  .svc-welders { left: 324px; top: 254px; }
  .suppliers-tab {
    position: absolute; left: 75px; top: 366px; width: 137px; height: 31px;
    background: var(--grey-dark); color: var(--white); font-family: "Montserrat", sans-serif;
    font-weight: 600; font-size: 8.5px; display: flex; align-items: center; justify-content: center;
    letter-spacing: 0.3px;
  }
  .supplier-list { position: absolute; left: 0; top: 413px; width: 820px; height: 22px; }
  .supplier { position: absolute; top: 0; line-height: 22px; transform: translateX(-50%);
    font-family: "Roboto", sans-serif; font-weight: 700; font-size: 13px;
    color: var(--grey-dark); letter-spacing: 0.4px; white-space: nowrap; }
  .hours { position: absolute; left: 910px; top: 382px; display: flex; align-items: center; gap: 13px; }
  .hours-icon { width: 34px; height: 34px; border-radius: 50%; background: var(--white);
    display: flex; align-items: center; justify-content: center; }
  .hours-text { color: var(--white); font-size: 11px; line-height: 19px; letter-spacing: 0.2px; }
</style>
</head>
<body>
<div class="banner">
  <svg class="banner-shapes" width="1200" height="450" viewBox="0 0 1200 450">
    <defs>
      <linearGradient id="header-fill" x1="0" y1="0" x2="1" y2="0">
        <stop offset="0" stop-color="#f6f6f6"/><stop offset="1" stop-color="#ececec"/>
      </linearGradient>
      <linearGradient id="panel-fill" x1="0" y1="0" x2="1" y2="0.3">
        <stop offset="0" stop-color="#d9471f"/>
        <stop offset="0.45" stop-color="#b4533a"/>
        <stop offset="1" stop-color="#5f5553"/>
      </linearGradient>
      <linearGradient id="photo-fill" x1="0" y1="0" x2="1" y2="1">
        <stop offset="0" stop-color="#1d2b3a"/>
        <stop offset="0.55" stop-color="#2a2c33"/>
        <stop offset="0.8" stop-color="#a3461b"/>
        <stop offset="1" stop-color="#3a2418"/>
      </linearGradient>
    </defs>
    <rect class="header-band" x="0" y="0" width="760" height="70" fill="url(#header-fill)"/>
    <polygon class="service-panel" role="img" aria-label="Orange-tinted photo of a welder at work with sparks"
      points="0,70 672,70 713,0 793,0 690,175 815,382 68,382 0,450" fill="url(#panel-fill)"/>
    <polygon class="hero-photo" role="img" aria-label="Photo of a welder in a helmet welding metal in a workshop with flying sparks"
      points="813,0 1200,0 1200,350 813,350 706,175" fill="url(#photo-fill)"/>
    <polygon class="corner-accent" points="1072,0 1137,0 1104,54" fill="var(--orange)"/>
    <polygon class="hours-band" points="820,365 1200,365 1200,433 860,433" fill="var(--grey-dark)"/>
    <polygon class="tab-ear" points="66,382 75,382 75,397" fill="#333"/>
    <polygon class="tab-ear" points="212,382 222,382 212,397" fill="#333"/>
  </svg>

  <div class="brand">
    <span class="brand-mark"></span>
    <span class="brand-name"><span class="line1">CORWICK</span><span class="line2">FUSION STORES</span></span>
  </div>

  <div class="contact contact-phone">
    <span class="contact-icon">
      <svg width="13" height="13" viewBox="0 0 24 24"><path fill="#fff" d="M6.6 10.8a15 15 0 0 0 6.6 6.6l2.2-2.2c.3-.3.7-.4 1-.2 1.1.4 2.3.6 3.6.6.6 0 1 .4 1 1V20c0 .6-.4 1-1 1C10.6 21 3 13.4 3 4c0-.6.4-1 1-1h3.5c.6 0 1 .4 1 1 0 1.3.2 2.5.6 3.6.1.3 0 .7-.2 1z"/></svg>
    </span>
    <span>07412 580 317</span>
  </div>
  <div class="contact contact-email">
    <span class="contact-icon">
      <svg width="13" height="11" viewBox="0 0 24 18"><path fill="#fff" d="M2 0h20a2 2 0 0 1 2 2v1L12 10 0 3V2a2 2 0 0 1 2-2zm-2 6l12 7 12-7v10a2 2 0 0 1-2 2H2a2 2 0 0 1-2-2z"/></svg>
    </span>
    <span>cfsarc@mailvane.net</span>
  </div>

  <h1 class="services-title">OUR CORE SERVICES</h1>

  <div class="service svc-gases">
    <div class="service-hex">
      <svg width="58" height="66" viewBox="0 0 58 66"><polygon points="29,0 58,16.5 58,49.5 29,66 0,49.5 0,16.5" fill="#fff"/>
        <path d="M29 17c5 6 9 10 9 15a9 9 0 0 1-18 0c0-3 2-6 4-8 0 3 2 5 3 5-1-4 0-8 2-12z" fill="var(--grey-dark)"/>
        <path d="M21 43v5h16v-5" stroke="var(--grey-dark)" stroke-width="2.5" fill="none"/></svg>
    </div>
    <span class="service-label">INDUSTRIAL GASES</span>
  </div>
  <div class="service svc-hire">
    <div class="service-hex">
      <svg width="58" height="66" viewBox="0 0 58 66"><polygon points="29,0 58,16.5 58,49.5 29,66 0,49.5 0,16.5" fill="#fff"/>
        <circle cx="27" cy="31" r="12" stroke="var(--orange)" stroke-width="3" fill="none"/>
        <line x1="36" y1="40" x2="43" y2="47" stroke="var(--orange)" stroke-width="3.5" stroke-linecap="round"/>
        <circle cx="27" cy="28" r="3.5" fill="var(--orange)"/>
        <path d="M20 38a7 6 0 0 1 14 0z" fill="var(--orange)"/></svg>
    </div>
    <span class="service-label">HIRE</span>
  </div>
  <div class="service svc-training">
    <div class="service-hex">
      <svg width="58" height="66" viewBox="0 0 58 66"><polygon points="29,0 58,16.5 58,49.5 29,66 0,49.5 0,16.5" fill="#fff"/>
        <circle cx="33" cy="37" r="8" stroke="var(--orange)" stroke-width="5" stroke-dasharray="3 2.3" fill="none"/>
        <circle cx="33" cy="37" r="6" stroke="var(--orange)" stroke-width="3" fill="none"/>
        <circle cx="20" cy="24" r="4.5" stroke="var(--orange)" stroke-width="3.5" stroke-dasharray="2 1.5" fill="none"/></svg>
    </div>
    <span class="service-label">TRAINING COURSES</span>
  </div>
  <div class="service svc-welders">
    <div class="service-hex">
      <svg width="58" height="66" viewBox="0 0 58 66"><polygon points="29,0 58,16.5 58,49.5 29,66 0,49.5 0,16.5" fill="#fff"/>
        <rect x="16" y="18" width="15" height="16" rx="4" fill="var(--grey-dark)"/>
        <rect x="19" y="23" width="9" height="4" fill="#fff"/>
        <path d="M13 48v-8a5 5 0 0 1 5-5h11a5 5 0 0 1 5 5v8z" fill="var(--grey-dark)"/>
        <rect x="38" y="26" width="3" height="14" fill="var(--grey-dark)"/>
        <rect x="36" y="40" width="8" height="8" fill="var(--grey-dark)"/></svg>
    </div>
    <span class="service-label">WELDERS &amp; CONSUMABLES</span>
  </div>

  <div class="suppliers-tab">OUR CORE SUPPLIERS</div>
  <div class="supplier-list">
    <span class="supplier" style="left:112px;">KORVEX</span>
    <span class="supplier" style="left:190px;">ALVANE</span>
    <span class="supplier" style="left:241px;">DUNE</span>
    <span class="supplier" style="left:305px;">HELMAR</span>
    <span class="supplier" style="left:373px;">TRX</span>
    <span class="supplier" style="left:436px;">FORGELINE</span>
    <span class="supplier" style="left:528px;">ZANTO</span>
    <span class="supplier" style="left:617px;">MIRWELD</span>
    <span class="supplier" style="left:708px;">QPT</span>
    <span class="supplier" style="left:787px;">NOL</span>
  </div>

  <div class="hours">
    <span class="hours-icon">
      <svg width="12" height="12" viewBox="0 0 24 24"><circle cx="12" cy="12" r="10" stroke="var(--orange)" stroke-width="3" fill="none"/><path d="M12 6v6h-4" stroke="var(--orange)" stroke-width="3" fill="none"/></svg>
    </span>
    <div class="hours-text">Monday to Friday 12:00 - 18:00<br>Saturday 09:00 - 12:00</div>
  </div>
</div>
</body>
</html>
```